Counseling Practice Business Card

I need a professional looking business card incorporating my new logo that was just completed. Card needs to incorporate my name and title, description of my specialty, my address, my phone number, my fax number, my email and my website URL. I need to be able to choose design on/with different paper colors and textures.
I do not have a lot of business card ideas so I am open to anything but I want bold,sharp, clear card without additional designs other than my logo (see attached file info). I am open to different color backgrounds or paper colors including black. I do not like traditional brackets around area codes in phone number or dashes between numbers in phone number. Am open to other ways of presenting including periods between numbers as appropriate. I do not know enough to know what I like yet but I want card to coordinate and work together with my logo. My practice emphasizes natural mental health interventions so any use of color (with background paper color or the blue and green in my logo) that elicits nature is nice. In addition to black, any natural brown or wood looking background might be desirable also. Most of the offerings so far look very similar and boring.

Target Market(s)

Potential therapy clients and other professionals

Contact Information for Business Card

Card information:
Gerald M. Whitcombe, Ph.D.
Licensed Clinical Psychologist
Integrative Health Coach
4812 Marlowe Ridge Blvd SE
Suite 310
Duluth, GA 30096
(770) 415-2983 phone
(770) 581-4096 fax
drgeraldwhitcombe@quillmarsh.net
brightfernwellness.net

Font styles to use
Serif
Sans Serif
Other font styles liked:
• anything that you think looks crisp, clear and easily readable

Requirements
Must have
• Any color used should coordinate with my logo design (see attached files).
• Card should be printed horizontally so top and bottom are longest sides of rectangle.
• Background color or paper color should complement and highlight logo. Do not like a white background. black, grey, brown or any color my logo would blend well with.
Nice to have
• I would like designer to utilize color to highlight letters/name or phone-fax-web symbols.
• Bottom edge of card could be highlighted if appropriate to an idea.
Should not have
• I would NOT want the card to have a pure white background at all.
• No clear cards.
• Cards should be oriented with long sides on bottom and top, NOT sides. DO NOT LIKE THIS THIN TALL ORIENTATION.

```html
<!DOCTYPE html>
<html lang="en">
<head>
<meta charset="utf-8">
<title>Brightfern Wellness – Business Card</title>
<link rel="stylesheet" href="https://fonts.googleapis.com/css2?family=Roboto+Condensed:wght@400;500;700&family=Roboto:wght@400&display=swap">
<style>
  :root {
    --backdrop: #6f4a30;
    --card-green: #016a36;
    --card-blue: #2873b8;
    --ink: #161a1f;
    --card-black: #141518;
    --brand-blue: #2a72b5;
  }
  html, body {
    margin: 0;
    padding: 0;
    width: 1200px;
    height: 960px;
    overflow: hidden;
    background: var(--backdrop);
  }
  .canvas {
    position: relative;
    width: 1200px;
    height: 960px;
  }
  .card {
    position: absolute;
    width: 600px;
    height: 342px;
    overflow: hidden;
  }
  .card--front {
    left: 314px;
    top: 113px;
    background: var(--card-green);
  }
  .card--back {
    left: 312px;
    top: 472px;
    background: var(--card-black);
  }
  .front-field {
    position: absolute;
    inset: 0;
  }
  .identity {
    position: absolute;
    right: 38px;
    top: 26px;
    text-align: right;
    color: var(--ink);
    font-family: "Roboto Condensed", "Arial Narrow", sans-serif;
  }
  .identity__name {
    margin: 0;
    font-weight: 700;
    font-size: 20px;
    letter-spacing: 0.2px;
    text-transform: uppercase;
    line-height: 1.1;
  }
  .identity__title {
    margin: 0;
    font-size: 15.5px;
    font-weight: 400;
    line-height: 1.2;
  }
  .contact {
    position: absolute;
    right: 38px;
    top: 189px;
    text-align: right;
    color: var(--ink);
    font-family: "Roboto", Arial, sans-serif;
    font-size: 13.5px;
    line-height: 19px;
    font-style: normal;
  }
  .contact__address {
    margin: 0 0 10px;
  }
  .contact__lines {
    margin: 0;
  }
  .brand {
    position: absolute;
    margin: 0;
    font-family: "Roboto Condensed", "Arial Narrow", sans-serif;
    font-weight: 700;
    font-size: 30px;
    line-height: 30px;
    letter-spacing: 0.3px;
  }
  .brand--front {
    left: 98px;
    top: 254px;
    color: var(--ink);
  }
  .brand--back {
    right: 48px;
    top: 222px;
    text-align: right;
    color: var(--brand-blue);
  }
</style>
</head>
<body>
<main class="canvas">
  <section class="card card--front" aria-label="Card front">
    <svg class="front-field" width="600" height="342" viewBox="0 0 600 342" aria-hidden="true">
      <ellipse cx="400" cy="332" rx="420" ry="210" fill="var(--card-blue)"/>
    </svg>
    <header class="identity">
      <h1 class="identity__name">Gerald M. Whitcombe, Ph.D.</h1>
      <p class="identity__title">Licensed Clinical Psychologist</p>
      <p class="identity__title">Integrative Health Coach</p>
    </header>
    <address class="contact">
      <p class="contact__address">4812 Marlowe Ridge Blvd SE<br>Suite 310, Duluth, GA 30096</p>
      <p class="contact__lines">
        P: (770) 415-2983<br>
        F: (770) 581-4096<br>
        drgeraldwhitcombe@quillmarsh.net<br>
        www.brightfernwellness.net
      </p>
    </address>
    <p class="brand brand--front">Brightfern<br>Wellness</p>
  </section>

  <section class="card card--back" aria-label="Card back">
    <p class="brand brand--back">Brightfern<br>Wellness</p>
  </section>
</main>
</body>
</html>
```